Velvet Dice Night Age Verification Landing Page

To create a visually appealing design for the landing page of the adult game "Velvet Dice Night" that confirms the visitor's age.
The design should have a simple and visually appealing look that focuses on two buttons labeled "Yes" and "No". The purpose of the page is to confirm that the visitor is 18 years of age or older before accessing the game's content. Responsive design that works well on desktop and mobile devices. The final output should be delivered in PSD, AI, or Sketch format, along with any necessary images or assets.
I have also attached examples.

```html
<!DOCTYPE html>
<html lang="en">
<head>
<meta charset="utf-8">
<title>Velvet Dice Night – Age Verification</title>
<link href="https://fonts.googleapis.com/css2?family=Montserrat:wght@500;700;800&display=swap" rel="stylesheet">
<style>
  :root {
    --bg-top: #4c1490;
    --bg-mid: #7a2aa6;
    --bg-bottom: #b52ba8;
    --panel: rgba(22, 10, 28, 0.82);
    --text: #ffffff;
    --btn-yes: #c410c4;
    --btn-no: #6a0ad0;
    --check: #3bbf3b;
  }
  * { box-sizing: border-box; margin: 0; padding: 0; }
  html, body {
    width: 1200px;
    height: 771px;
    overflow: hidden;
    font-family: "Montserrat", sans-serif;
    color: var(--text);
  }
  .page {
    position: relative;
    width: 1200px;
    height: 771px;
  }
  .hero-backdrop {
    position: absolute;
    inset: 0;
    background:
      radial-gradient(ellipse at 55% 45%, rgba(60, 20, 50, 0.55), transparent 60%),
      linear-gradient(180deg, var(--bg-top) 0%, var(--bg-mid) 50%, var(--bg-bottom) 100%);
  }
  .age-panel {
    position: absolute;
    left: 231px;
    top: 185px;
    width: 739px;
    height: 409px;
    background: var(--panel);
    border-radius: 8px;
    text-align: center;
  }
  .brand {
    position: absolute;
    top: 62px;
    left: 0;
    right: 0;
    display: flex;
    align-items: center;
    justify-content: center;
    gap: 10px;
    font-weight: 700;
    font-size: 24px;
  }
  .brand-dot {
    width: 14px;
    height: 14px;
    border-radius: 50%;
    background: var(--text);
  }
  .age-question {
    position: absolute;
    top: 188px;
    left: 0;
    right: 0;
    font-weight: 700;
    font-size: 21px;
  }
  .choice-buttons {
    position: absolute;
    top: 250px;
    left: 0;
    right: 0;
    display: flex;
    justify-content: center;
    gap: 25px;
  }
  .choice {
    width: 95px;
    height: 39px;
    border: none;
    border-radius: 5px;
    color: var(--text);
    font-family: "Montserrat", sans-serif;
    font-weight: 800;
    font-size: 15px;
  }
  .choice-yes { background: var(--btn-yes); }
  .choice-no { background: var(--btn-no); }
  .remember {
    position: absolute;
    top: 326px;
    left: 0;
    right: 0;
    display: flex;
    align-items: center;
    justify-content: center;
    gap: 8px;
    font-weight: 500;
    font-size: 15px;
  }
  .remember-box {
    width: 12px;
    height: 12px;
    background: #fff;
    border-radius: 2px;
    display: block;
  }
</style>
</head>
<body>
<main class="page">
  <div class="hero-backdrop" role="img" aria-label="Romantic photo of a couple embracing in bed, tinted purple to magenta"></div>

  <section class="age-panel">
    <div class="brand"><span class="brand-dot"></span>Velvet Dice Night</div>
    <h1 class="age-question">Are You over 18 Years Of Age?</h1>
    <div class="choice-buttons">
      <button class="choice choice-yes">Yes</button>
      <button class="choice choice-no">No</button>
    </div>
    <label class="remember">
      <svg class="remember-box" viewBox="0 0 12 12" aria-hidden="true">
        <rect width="12" height="12" rx="2" fill="#fff"/>
        <rect x="1.5" y="1.5" width="9" height="9" rx="1" fill="var(--check)"/>
        <path d="M3.3 6.2 L5.2 8 L8.8 4.2" fill="none" stroke="#fff" stroke-width="1.5"/>
      </svg>
      Remember Me
    </label>
  </section>
</main>
</body>
</html>
```